RW Framewell Inc Business cards

We need business cards using our existing logo but slightly modified. Right now the logo says RW Loadbearing Masonry. We want to keep the RW part of the design, but replace the Structural Concrete portion with "FRAMEWELL". Please see the attached file.
Ideally this would be a blank template so we can add Different Names, titles, and phone numbers later.
On the one side we want only the logo and on the other side the detail. I'm attaching an example for you to see.
Please reach out with any other questions. Our address and other details will be given out once we find a design we like.

Target Market(s)

Construction Industry

```html
<!DOCTYPE html>
<html lang="en">
<head>
<meta charset="utf-8">
<title>RW Framewell Inc — Business Cards</title>
<link rel="stylesheet" href="https://fonts.googleapis.com/css2?family=Montserrat:wght@600;700&family=Roboto:wght@400;500;700&display=swap">
<style>
  :root {
    --stage: #3b3b3d;
    --card: #1f2022;
    --card-soft: #26272a;
    --brand-blue: #2f64ab;
    --steel-grey: #8a8b8d;
    --text-light: #f2f2f2;
    --ghost: #2b2c2f;
  }
  * { margin: 0; padding: 0; box-sizing: border-box; }
  html, body {
    width: 799px; height: 1200px; overflow: hidden;
    background: var(--stage);
  }
  .sheet {
    position: relative; width: 799px; height: 1200px;
    display: flex; flex-direction: column; align-items: center; justify-content: center; gap: 110px;
  }
  .card {
    position: relative; width: 560px; height: 330px;
    background: var(--card); border-radius: 4px; overflow: hidden;
    box-shadow: 0 14px 30px rgba(0,0,0,0.45);
  }

  /* Front: logo only */
  .card-front { display: flex; align-items: center; justify-content: center; }
  .wordmark-front {
    display: flex; align-items: center; gap: 14px;
    font-family: "Montserrat", sans-serif; font-weight: 700;
    font-size: 40px; letter-spacing: 4px; color: #7b7c7f;
  }
  .wordmark-front .mark-square { width: 26px; height: 26px; background: #55565a; }

  /* Back: details */
  .wordmark-back {
    position: absolute; left: 34px; top: 40px;
    display: flex; align-items: center; gap: 12px;
    font-family: "Montserrat", sans-serif; font-weight: 700;
    font-size: 30px; letter-spacing: 3px; color: var(--text-light);
  }
  .wordmark-back .mark-square { width: 22px; height: 22px; background: var(--brand-blue); }

  .ghost-initials {
    position: absolute; right: 18px; top: 118px;
    font-family: "Montserrat", sans-serif; font-weight: 700;
    font-size: 150px; line-height: 1; color: var(--ghost);
  }

  .person { position: absolute; left: 34px; top: 170px; font-family: "Roboto", sans-serif; }
  .person-name { font-size: 21px; font-weight: 700; color: var(--brand-blue); }
  .person-title { font-size: 13px; color: var(--text-light); margin-top: 3px; }

  .contact {
    position: absolute; left: 292px; top: 176px;
    font-family: "Roboto", sans-serif; font-size: 13px; color: var(--text-light);
    list-style: none; line-height: 1.5;
  }
  .contact li { display: flex; align-items: flex-start; gap: 8px; }
  .contact svg { width: 12px; height: 12px; margin-top: 4px; flex-shrink: 0; }
  .contact .address { padding-left: 20px; }

  .accent-grey {
    position: absolute; left: 0; bottom: 54px; width: 260px; height: 12px;
    background: var(--steel-grey);
  }
  .accent-blue {
    position: absolute; right: 0; bottom: 0; width: 320px; height: 70px;
    background: var(--brand-blue); border-top-left-radius: 26px;
    display: flex; align-items: center; justify-content: center;
    font-family: "Roboto", sans-serif; font-weight: 700; font-size: 17px; color: #ffffff;
  }
</style>
</head>
<body>
<main class="sheet">
  <section class="card card-front" aria-label="Card front">
    <div class="wordmark-front"><span class="mark-square"></span>RW FRAMEWELL</div>
  </section>

  <section class="card card-back" aria-label="Card back">
    <div class="ghost-initials" aria-hidden="true">RW</div>
    <div class="wordmark-back"><span class="mark-square"></span>RW FRAMEWELL</div>

    <div class="person">
      <p class="person-name">Mark RW Ellison</p>
      <p class="person-title">Managing Director</p>
    </div>

    <ul class="contact">
      <li>
        <svg viewBox="0 0 24 24" fill="var(--brand-blue)"><path d="M6.6 10.8a15.1 15.1 0 0 0 6.6 6.6l2.2-2.2a1 1 0 0 1 1-.25 11.4 11.4 0 0 0 3.6.57 1 1 0 0 1 1 1V20a1 1 0 0 1-1 1A17 17 0 0 1 3 4a1 1 0 0 1 1-1h3.5a1 1 0 0 1 1 1c0 1.25.2 2.45.57 3.57a1 1 0 0 1-.25 1z"/></svg>
        <span>555-014-2086</span>
      </li>
      <li>
        <svg viewBox="0 0 24 24" fill="var(--brand-blue)"><path d="M2 5h20v14H2z M2 5l10 8 10-8" stroke="var(--card)" stroke-width="1.5"/></svg>
        <span>mark@framewellbuild.com</span>
      </li>
      <li class="address">418 Beamline Ave., Oak Ridge,<br>California, US 90217</li>
    </ul>

    <div class="accent-grey"></div>
    <div class="accent-blue">www.framewellbuild.com</div>
  </section>
</main>
</body>
</html>
```